Wordpress Website design partner needed for an Arabic Language Institute for English Speakers

We are an online Arabic Language institute, targeting English Speakers around the world and we provide online courses and private group and one on one classes
We are looking for a total of 5 pages designed.
The Design should be mobile-first, and then provide PC for any differences.
I am looking for a consistent design with a lot of white space and in line with our Logo colours.
Images used should be around the theme of Arabic Language/Islamic in Nature, so please do not use any illustrations or images of animals or human beings except for silhouettes or images without faces visible, such as someone facing other way or below torso or hands etc.
The website will eventually be prepared for Wordpress using Divi.
I will provide a very structured outline of what elements and modules each page should have. Therefore I am looking for someone that has an eye for detail and is precise in executing requirements.
I decided to post on this site because I am looking for a long-term partner that can take care of any of our design needs as they come up.
More details to follow
I will do abit more research tomorrow to suggest sample sites
Updates
Target Market(s)
English speakers that want to learn Arabic for Religous purposes such as understanding the Quran
Industry/Entity Type
Education
Colors
Designer to choose colors to be used in the design.
Requirements
Must have
- Mobile First, and design for PC for changes
- Consistency
- Plenty of White Space
- Colour Palette based on Logo
- Colour and Transparent/White Header for when scrolling
- Big Call to Action buttons with contrasting colors
- A consistent footer for all pages with
- -Social Media Icons
- -Contact us
- -Sitemap
- -Copyright
- -Logo
- Anything with a hashtag (#) beforehand in the Doc file means it should be a module like the modules used in Divi Theme, Please check the following website for an explanation of what each module consists of and some examples of it in use. https://www.pelmorashowcase.net/pelmora-blocks-guide/
Nice to have
- Parallax Effect
Should not have
- illustrations or images of animals or human beings except for silhouettes or images without faces visible, such as someone facing other way or below torso or hands etc.

```html
<!DOCTYPE html>
<html lang="en">
<head>
<meta charset="utf-8">
<title>Al-Manar Academy – Learn Arabic</title>
<link href="https://fonts.googleapis.com/css2?family=Lato:wght@400;700&display=swap" rel="stylesheet">
<style>
:root{
  --blue:#1d5c9e;
  --teal:#2a93aa;
  --teal-flat:#2595a8;
  --orange:#f7941d;
  --ink:#222;
  --text:#444;
  --muted:#666;
  --grey-bg:#f3f3f3;
  --footer:#242424;
  --white:#fff;
}
*{box-sizing:border-box;margin:0;padding:0}
html,body{width:1200px;height:4248px;overflow:hidden;background:var(--white)}
body{font-family:'Lato',sans-serif;color:var(--text);position:relative}
.abs{position:absolute}
.wrap{position:absolute;left:74px;width:1052px}

/* header */
.site-header{top:0;left:0;width:1200px;height:111px;background:var(--white);position:absolute}
.brand{position:absolute;left:74px;top:20px;display:flex;align-items:center;gap:10px}
.brand-mark{width:22px;height:22px;background:var(--teal);border-radius:4px}
.brand-name{font-weight:700;font-size:20px;color:var(--blue);line-height:1.1}
.main-nav{position:absolute;right:74px;top:50px;display:flex;gap:47px;font-size:16px;font-weight:700;color:var(--ink)}
.main-nav a{text-decoration:none;color:inherit;position:relative;padding-bottom:12px}
.main-nav a.active{color:var(--blue)}
.main-nav a.active::after{content:"";position:absolute;left:-12px;right:-12px;bottom:0;height:3px;background:var(--blue)}

/* intro band */
.intro{position:absolute;top:111px;left:0;width:1200px;height:225px;background:linear-gradient(90deg,#1c5a9b,#2784ab)}
.intro p{position:absolute;left:74px;top:34px;width:800px;color:var(--white);font-size:27px;line-height:40px}
.btn{display:inline-flex;align-items:center;justify-content:center;background:var(--orange);color:var(--white);font-weight:700;border-radius:30px;text-decoration:none}
.intro .btn{position:absolute;left:870px;top:87px;width:256px;height:53px;font-size:22px;box-shadow:0 3px 8px rgba(0,0,0,.2)}

/* slider */
.slider{top:369px;height:490px;background:linear-gradient(135deg,#3a3430,#6b5a4a 45%,#2b2b2d);overflow:hidden}
.slider h2{position:absolute;top:155px;left:0;right:0;text-align:center;color:var(--white);font-weight:400;font-size:36px;line-height:48px}
.slider .btn-outline{position:absolute;top:276px;left:436px;width:180px;height:50px;border:3px solid var(--white);border-radius:28px;color:var(--white);font-size:18px;display:flex;align-items:center;justify-content:center}
.slider svg.arrow{position:absolute;top:225px}

/* section titles */
.sec-title{position:absolute;left:0;width:1200px;text-align:center;font-size:33px;font-weight:700;color:var(--ink)}
.sec-title::after{content:"";display:block;width:56px;height:3px;background:var(--blue);margin:12px auto 0}

/* benefits */
.benefits{top:1005px;height:228px;display:flex;justify-content:space-between}
.benefit{width:330px;text-align:center;padding-top:26px}
.benefit.raised{background:var(--white);box-shadow:0 2px 12px rgba(0,0,0,.18)}
.benefit .icon{width:64px;height:64px;margin:0 auto;background:linear-gradient(135deg,#2d6fb0,#2a9bb0);border-radius:10px;opacity:.85}
.benefit h3{color:var(--blue);font-size:21px;margin:14px 0 10px}
.benefit p{font-size:14px;line-height:25px;color:var(--muted);padding:0 16px}

/* testimonials */
.band-grey{position:absolute;left:0;width:1200px;background:var(--grey-bg)}
.testimonials{top:1463px;height:164px;display:flex;justify-content:space-between}
.testimonial{width:513px;height:164px;background:linear-gradient(90deg,#1c5a9b,#2a93aa);display:flex;align-items:center;padding:0 24px;gap:24px;color:var(--white)}
.avatar{width:112px;height:112px;border-radius:50%;background:radial-gradient(circle at 50% 40%,#3a3a3a 0 35%,#fff 36%);flex:none}
.testimonial p{font-size:14px;line-height:25px}
.testimonial .name{font-weight:700;font-size:16px;margin-top:4px}
.testimonial .co{font-size:12px;opacity:.85}

/* strategies */
.strategies-title{position:absolute;top:1727px;left:0;width:1200px;text-align:center;font-size:33px;line-height:41px;font-weight:700;color:var(--ink)}
.strategies-title::after{content:"";display:block;width:56px;height:3px;background:var(--blue);margin:18px auto 0}
.strategies-copy{position:absolute;top:1850px;left:150px;width:900px;text-align:center;font-size:14px;line-height:25px;color:var(--muted)}
.book{position:absolute;top:1931px;left:509px;width:180px;height:52px;font-size:19px}
.countdown{position:absolute;top:2019px;left:165px;width:872px;height:173px;background:var(--teal-flat);color:var(--white);text-align:center}
.countdown h3{font-weight:400;font-size:28px;margin-top:26px}
.count-row{display:flex;justify-content:center;align-items:flex-start;gap:28px;margin-top:16px}
.unit{width:94px}
.unit b{display:block;font-weight:400;font-size:37px;line-height:40px}
.unit span{font-size:17px}
.sep{font-size:28px;line-height:60px}

/* features */
.accordion{position:absolute;left:252px;width:694px}
.acc-item{height:53px;background:var(--white);border:1px solid #e2e2e2;display:flex;align-items:center;justify-content:space-between;padding:0 18px;font-weight:700;font-size:18px;color:var(--ink)}
.acc-open{height:158px;background:var(--white);border:1px solid #e2e2e2;padding:14px 18px}
.acc-open h4{display:flex;justify-content:space-between;color:var(--blue);font-size:18px}
.acc-open p{font-size:14px;line-height:25px;color:var(--muted);margin-top:14px}

/* video */
.video{position:absolute;top:3029px;left:254px;width:690px;height:349px;border:5px solid #ddd;background:linear-gradient(135deg,#3c3c3c,#6e6e6e 55%,#4a4a4a)}
.video svg{position:absolute;left:310px;top:135px}

/* partners */
.partners{position:absolute;top:3455px;left:174px;width:852px;display:flex;justify-content:space-between;align-items:center}
.partner{display:flex;align-items:center;gap:10px;font-size:36px;font-weight:700;color:#8a8a8a}
.partner i{width:36px;height:36px;background:#9a9a9a;border-radius:50%;display:block}

/* contact */
.contact{position:absolute;top:3573px;left:74px;width:1052px;height:320px;background:linear-gradient(90deg,#1c5a9b,#2a93aa);color:var(--white)}
.contact h2{position:absolute;left:40px;top:70px;font-size:33px;font-weight:400}
.contact h2::after{content:"";display:block;width:56px;height:3px;background:var(--white);margin-top:12px}
.contact p{position:absolute;left:40px;top:150px;width:480px;font-size:14px;line-height:25px}
.form{position:absolute;left:606px;top:40px;width:383px}
.field{height:48px;background:var(--white);color:var(--ink);font-size:14px;font-weight:700;padding:0 16px;display:flex;align-items:center;margin-bottom:16px}
.join{height:48px;border:2px solid var(--white);display:flex;align-items:center;justify-content:center;font-size:22px}

/* footer */
.site-footer{position:absolute;top:3955px;left:0;width:1200px;height:293px;background:var(--footer);color:#ddd}
.f-brand{position:absolute;left:74px;top:60px}
.f-brand .brand-name{color:var(--white)}
.f-copy{position:absolute;left:74px;top:172px;font-size:12px;line-height:23px}
.f-col{position:absolute;top:58px}
.f-col h4{font-size:19px;font-weight:700;color:var(--white);margin-bottom:12px}
.f-col li{list-style:none;font-size:13px;line-height:33px}
.f-contact li{line-height:25px;display:flex;gap:14px;align-items:center}
.social{display:flex;gap:16px;margin-top:6px}
.social span{width:20px;height:20px;border-radius:50%;background:#ddd;display:block}
</style>
</head>
<body>

<header class="site-header">
  <div class="brand"><span class="brand-mark"></span><span class="brand-name">Al-Manar<br>Academy</span></div>
  <nav class="main-nav">
    <a class="active" href="#">Home</a><a href="#">About Us</a><a href="#">Course</a><a href="#">Our Courses</a><a href="#">Contact Us</a>
  </nav>
</header>

<section class="intro">
  <p>The Arabic Language Academy which helps understand Allah’s words and the Noble Prophets teachings directly in the most Effective, Efficient and Effortless way. Never rely on translations again!</p>
  <a class="btn" href="#">Start Learning Now</a>
</section>

<section class="wrap slider" role="img" aria-label="Hands typing on a laptop showing a Learn Arabic screen">
  <svg class="arrow" style="left:14px" width="24" height="40" viewBox="0 0 24 40"><path d="M20 4 6 20l14 16" fill="none" stroke="#fff" stroke-width="5"/></svg>
  <h2>Pellentesque tempor, sem sit amet porttitor<br>pellentesque tellus metus</h2>
  <span class="btn-outline">Learn More</span>
  <svg class="arrow" style="right:14px" width="24" height="40" viewBox="0 0 24 40"><path d="M4 4l14 16L4 36" fill="none" stroke="#fff" stroke-width="5"/></svg>
</section>

<h2 class="sec-title" style="top:914px">Benefits</h2>
<section class="wrap benefits">
  <div class="benefit raised"><div class="icon" role="img" aria-label="Checklist and clock icon"></div><h3>Efficient</h3><p>Sed ac dui lectus. Proin augue tellus, rutrum sed congue sed, condimentum eget varius natoque penatibus.</p></div>
  <div class="benefit"><div class="icon" role="img" aria-label="Monitor with target icon"></div><h3>Effective</h3><p>Sed ac dui lectus. Proin augue tellus, rutrum sed congue sed, condimentum eget varius natoque penatibus.</p></div>
  <div class="benefit"><div class="icon" role="img" aria-label="Relaxed desk icon"></div><h3>Effortless</h3><p>Sed ac dui lectus. Proin augue tellus, rutrum sed congue sed, condimentum eget varius natoque penatibus.</p></div>
</section>

<div class="band-grey" style="top:1328px;height:360px"></div>
<h2 class="sec-title" style="top:1370px">Testimonial</h2>
<section class="wrap testimonials">
  <div class="testimonial"><div class="avatar" role="img" aria-label="Silhouette avatar"></div><div><p>Aliquam laoreet, tortor nec interdum scelerisque, purus leo ultricies sapien, vel sodales nulla dui nec odio. Ut sed placerat velit, sed convallis tortor.</p><div class="name">Name Heading</div><div class="co">Company Name</div></div></div>
  <div class="testimonial"><div class="avatar" role="img" aria-label="Silhouette avatar"></div><div><p>Aliquam laoreet, tortor nec interdum scelerisque, purus leo ultricies sapien, vel sodales nulla dui nec odio. Ut sed placerat velit, sed convallis tortor.</p><div class="name">Name Heading</div><div class="co">Company Name</div></div></div>
</section>

<h2 class="strategies-title">7 Learning Strategies that will boost your Arabic<br>Learning Instantly</h2>
<p class="strategies-copy">Proin augue tellus, rutrum sed congue sed, condimentum eget varius natoque penatibus. magna ac sapien vulputate dapibus.<br>Curabitur placerat mollis arcu, quis pretium quam ultrices id ultrices ante a egestas congue.</p>
<a class="btn book" href="#">Book Your Spot</a>
<section class="countdown">
  <h3>Launching In</h3>
  <div class="count-row">
    <div class="unit"><b>000</b><span>Days</span></div><div class="sep">:</div>
    <div class="unit"><b>000</b><span>Days</span></div><div class="sep">:</div>
    <div class="unit"><b>000</b><span>Days</span></div><div class="sep">:</div>
    <div class="unit"><b>000</b><span>Days</span></div>
  </div>
</section>

<div class="band-grey" style="top:2264px;height:615px"></div>
<h2 class="sec-title" style="top:2306px">Features</h2>
<div class="accordion" style="top:2398px">
  <div class="acc-item">24/7 Access<svg width="16" height="16" viewBox="0 0 16 16"><circle cx="8" cy="8" r="8" fill="#222"/><path d="M6.5 4.5 10 8l-3.5 3.5" stroke="#fff" stroke-width="2" fill="none"/></svg></div>
</div>
<div class="accordion" style="top:2462px">
  <div class="acc-item">Learn at your own Pace<svg width="16" height="16" viewBox="0 0 16 16"><circle cx="8" cy="8" r="8" fill="#222"/><path d="M6.5 4.5 10 8l-3.5 3.5" stroke="#fff" stroke-width="2" fill="none"/></svg></div>
</div>
<div class="accordion" style="top:2525px">
  <div class="acc-item">Certificate<svg width="16" height="16" viewBox="0 0 16 16"><circle cx="8" cy="8" r="8" fill="#222"/><path d="M6.5 4.5 10 8l-3.5 3.5" stroke="#fff" stroke-width="2" fill="none"/></svg></div>
</div>
<div class="accordion" style="top:2589px">
  <div class="acc-item">Free Study Material<svg width="16" height="16" viewBox="0 0 16 16"><circle cx="8" cy="8" r="8" fill="#222"/><path d="M6.5 4.5 10 8l-3.5 3.5" stroke="#fff" stroke-width="2" fill="none"/></svg></div>
</div>
<div class="accordion" style="top:2652px">
  <div class="acc-open"><h4>Qualified Teachers<svg width="16" height="16" viewBox="0 0 16 16"><circle cx="8" cy="8" r="8" fill="#1d5c9e"/><path d="M4.5 6.5 8 10l3.5-3.5" stroke="#fff" stroke-width="2" fill="none"/></svg></h4>
  <p>Proin augue tellus, rutrum sed congue sed, condimentum eget varius natoque penatibus. magna ac sapien vulputate dapibus. Curabitur placerat mollis arcu, quis pretium quam ultrices id ultrices ante a egestas congue.</p></div>
</div>

<h2 class="sec-title" style="top:2933px">Watch Video</h2>
<div class="video" role="img" aria-label="Video still of Arabic writing on a chalkboard">
  <svg width="70" height="70" viewBox="0 0 70 70"><circle cx="35" cy="35" r="33" fill="#fff"/><path d="M27 20v30l24-15z" fill="#222"/></svg>
</div>

<div class="partners">
  <div class="partner"><i></i>PostHive</div>
  <div class="partner"><i></i>MailRiver</div>
  <div class="partner"><i></i>FeedLane</div>
</div>

<section class="contact">
  <h2>Get In Touch</h2>
  <p>Proin augue tellus, rutrum sed congue sed, condimentum eget varius natoque penatibus. magna ac sapien vulputate dapibus. Curabitur placerat mollis arcu, quis pretium quam ultrices id ultrices ante a egestas congue.</p>
  <div class="form">
    <div class="field">First Name</div>
    <div class="field">Last Name</div>
    <div class="field">Email Address</div>
    <div class="join">Join Now</div>
  </div>
</section>

<footer class="site-footer">
  <div class="f-brand brand" style="position:absolute"><span class="brand-mark"></span><span class="brand-name">Al-Manar<br>Academy</span></div>
  <div class="f-copy">Copyright © 2019, Company Name<br>All Right reserved</div>
  <div class="f-col" style="left:355px"><h4>Site Map</h4><ul><li>Home</li><li>About Us</li><li>Course</li><li>Our Courses</li><li>Contact Us</li></ul></div>
  <div class="f-col f-contact" style="left:591px"><h4>Contact Us</h4><ul>
    <li>418 Cedar Ridge Road<br>Suite 20 Dunmore,<br>OR 97310</li>
    <li><svg width="14" height="14" viewBox="0 0 14 14"><path d="M3 1l3 3-2 2a8 8 0 0 0 4 4l2-2 3 3-2 2C5 13 1 9 1 3z" fill="#ddd"/></svg>1-800-555-0142</li>
    <li><svg width="14" height="12" viewBox="0 0 14 12"><rect width="14" height="12" fill="#ddd"/><path d="M0 1l7 5 7-5" stroke="#242424" fill="none"/></svg>hello@almanar-academy.org</li>
  </ul></div>
  <div class="f-col" style="left:886px"><h4>Follow Us</h4>
    <div class="social" role="img" aria-label="Social media links"><span></span><span></span><span></span><span></span><span></span></div>
  </div>
</footer>

</body>
</html>
```